Company Business Cards 2014

I need six different types of business cards. Two general cards for our two locations, along with four different employee cards. I have attached our logo and pictures of the cards we have now.

Front of each employee card should be glossy and have facebook and instagram logos.
Front of each general business card should be matte and have a space for salespersons name, along with facebook and instagram logs.
Back of each card should be matte and have a space for a quote (as the one attached).

We are open to different pictures of big off road trucks, tires and or wheels

Can you please put something together and email me your design details?

1. Company Info:(General Business Card)

RW WHEEL & LIFT
4827 N. BRAMBLE FIELD DR.
CORPUS CHRISTI, TX 78416
(361) 555-0147 Phone
(361) 555-0198 Fax
WWW.RWWHEELWORKS.NET

2. Employee Card:

Marla Quintrell
President
4827 N. Bramble Field Dr.
Corpus Christi, TX 78416
(361) 555-0147
marla@rwwheelworks.net

3. Employee Card:

Brent Oakes
Manager
4827 N. Bramble Field Dr.
Corpus Christi, TX 78416
(361) 555-0147 Office
(936-555-0163 Cell
brent@rwwheelworks.net

4. Employee Card:

Tessa Van Der Holt
Office Manager
4827 N. Bramble Field Dr.
Corpus Christi, TX 78416
(361) 555-0147 Office
tessa@rwwheelworks.net

5. Company Info:(General Business Card)

RW WHEEL & LIFT
734 FM ROAD 18 NORTH
LIVINGSTON, TX 77351
(936) 555-0182
WWW.RWWHEELWORKS.NET

6. Employee Card:

Grady Pelfrey
Manager
734 FM Road 18 North
Livingston, TX 77351
(936) 555-0182
rwwheel@mailbarn.example

Can you make the front of the cards Black with Green Lettering on your designs? Back of Card will need to be White with a space for a quote. 

Thanks

```html
<!DOCTYPE html>
<html lang="en">
<head>
<meta charset="utf-8">
<title>RW Wheel &amp; Lift — Business Card</title>
<link href="https://fonts.googleapis.com/css2?family=Saira+Condensed:wght@700&family=Exo+2:wght@400;600;800&display=swap" rel="stylesheet">
<style>
  :root{
    --accent-green:#3fbf3a;
    --letter-green:#5fe04f;
    --front-black:#0b0b0b;
    --front-shade:#1d1d1d;
    --ring-black:#000000;
    --paper:#ffffff;
    --paper-shade:#e4e4e4;
    --quote-line:#c9c9c9;
    --stage:#eceae6;
  }
  *{margin:0;padding:0;box-sizing:border-box}
  html,body{width:1200px;height:1019px;overflow:hidden;background:var(--stage)}
  .canvas{position:relative;width:1200px;height:1019px}
  .card{position:absolute;left:180px;width:840px;height:480px;overflow:hidden;box-shadow:0 6px 18px rgba(0,0,0,.18)}
  .card--front{top:20px}
  .card--back{top:520px}
  .card__art{position:absolute;inset:0;width:100%;height:100%}

  .holder{position:absolute;right:70px;top:42px;text-align:right}
  .holder__name{font-family:"Saira Condensed",sans-serif;font-weight:700;font-size:44px;letter-spacing:1px;color:var(--letter-green);line-height:1}
  .holder__title{font-family:"Exo 2",sans-serif;font-weight:600;font-size:22px;color:var(--letter-green);margin-top:4px}

  .contacts{position:absolute;right:40px;top:150px;list-style:none;font-family:"Exo 2",sans-serif;font-size:17px;color:var(--letter-green)}
  .contacts li{display:flex;justify-content:flex-end;align-items:center;gap:12px;height:30px}
  .contacts svg{width:16px;height:16px;fill:var(--letter-green)}
  .contacts .icon-gap{display:inline-block;width:16px}

  .social{position:absolute;right:40px;top:318px;display:flex;gap:10px}
  .social__spot{width:22px;height:22px;border-radius:50%;background:var(--accent-green)}

  .brand{position:absolute;left:90px;top:370px;display:flex;align-items:center;gap:12px}
  .brand__mark{width:26px;height:26px;background:var(--accent-green)}
  .brand__name{font-family:"Exo 2",sans-serif;font-weight:800;font-size:30px;color:var(--letter-green);letter-spacing:.5px}

  .quote-space{position:absolute;left:200px;top:150px;width:440px;height:150px;border-top:1px solid var(--quote-line);border-bottom:1px solid var(--quote-line)}
</style>
</head>
<body>
<main class="canvas">

  <section class="card card--front" aria-label="Card front">
    <svg class="card__art" viewBox="0 0 840 480" aria-hidden="true">
      <defs>
        <linearGradient id="frontShade" x1="0" y1="0" x2="0" y2="1">
          <stop offset="0" stop-color="var(--front-shade)"/>
          <stop offset="1" stop-color="var(--front-black)"/>
        </linearGradient>
      </defs>
      <rect width="840" height="480" fill="var(--accent-green)"/>
      <circle cx="262" cy="262" r="262" fill="var(--ring-black)"/>
      <path d="M290 0 H840 V370 L770 480 H290 A240 240 0 0 1 290 0 Z" fill="url(#frontShade)"/>
      <path d="M840 370 L770 480 H840 Z" fill="var(--accent-green)"/>
    </svg>

    <header class="holder">
      <h1 class="holder__name">MARLA QUINTRELL</h1>
      <p class="holder__title">President</p>
    </header>

    <ul class="contacts">
      <li>(361) 555-0147
        <svg viewBox="0 0 16 16"><path d="M3 1h3l1 4-2 1a9 9 0 0 0 5 5l1-2 4 1v3c0 1-1 2-2 2A13 13 0 0 1 1 3c0-1 1-2 2-2z"/></svg></li>
      <li>marla@rwwheelworks.net
        <svg viewBox="0 0 16 16"><path d="M0 3h16v10H0zm1 1v1l7 4 7-4V4z"/></svg></li>
      <li>www.rwwheelworks.net
        <svg viewBox="0 0 16 16"><path d="M8 0a8 8 0 1 0 0 16A8 8 0 0 0 8 0zm0 1.5c1 0 2 2 2.2 5.5H5.8C6 3.5 7 1.5 8 1.5zM1.6 7h3c0 2 .4 3.8 1 5.2A6.5 6.5 0 0 1 1.6 7zm9.8 0h3a6.5 6.5 0 0 1-4 5.2c.6-1.4 1-3.2 1-5.2zM5.8 8.5h4.4c-.2 3.5-1.2 6-2.2 6s-2-2.5-2.2-6z"/></svg></li>
      <li>4827 N. Bramble Field Dr.
        <svg viewBox="0 0 16 16"><path d="M8 0a5.5 5.5 0 0 0-5.5 5.5C2.5 10 8 16 8 16s5.5-6 5.5-10.5A5.5 5.5 0 0 0 8 0zm0 3a2.5 2.5 0 1 1 0 5 2.5 2.5 0 0 1 0-5z"/></svg></li>
      <li>Corpus Christi, TX 78416 <span class="icon-gap"></span></li>
    </ul>

    <div class="social" aria-label="Social media">
      <span class="social__spot"></span>
      <span class="social__spot"></span>
    </div>

    <div class="brand">
      <span class="brand__mark" aria-hidden="true"></span>
      <span class="brand__name">RW WHEEL &amp; LIFT</span>
    </div>
  </section>

  <section class="card card--back" aria-label="Card back">
    <svg class="card__art" viewBox="0 0 840 480" aria-hidden="true">
      <defs>
        <radialGradient id="backShade" cx=".5" cy=".35" r=".7">
          <stop offset="0" stop-color="var(--paper)"/>
          <stop offset=".8" stop-color="#f3f3f3"/>
          <stop offset="1" stop-color="var(--paper-shade)"/>
        </radialGradient>
      </defs>
      <rect width="840" height="480" fill="var(--paper)"/>
      <path d="M0 0 H120 L0 140 Z M840 480 H720 L840 340 Z" fill="var(--accent-green)"/>
      <ellipse cx="420" cy="250" rx="360" ry="225" fill="var(--ring-black)"/>
      <ellipse cx="420" cy="235" rx="340" ry="205" fill="url(#backShade)"/>
    </svg>
    <div class="quote-space" aria-label="Space for quote"></div>
  </section>

</main>
</body>
</html>
```